Business Card for beauty technology startup

Design Glimora Business Card for a Beauty, based on the website identity and colors (https://www.glimora-example.com).
Glimora is a beauty tech startup that gathers helpful product info for beauty lovers and consumers (such as availability on stores, price range and product reviews) for makeup products. The card design must be young, colorful but clean, and very modern.

Target Market(s)

woman, 15-35

Industry/Entity Type

Cosmetics

Contact Information for Business Card

Full Name, address, phone

Font styles to use
Other font styles liked:
• Advent Pro

Colors
e34297
86cfc6
ffffff
5c5c5c
e8e8e8
e667a6
b2b2b2

Requirements
Must have
• One full colored side with a creative design and another with card info
• Use Color palette: #95C5C5 and/or #D38AA5
• Use fonts: Advent Pro
• Use website identity: https://www.glimora-example.com
Nice to have
• If needed extra font: Roboto

```html
<!DOCTYPE html>
<html lang="en">
<head>
<meta charset="UTF-8">
<title>Glimora Business Card</title>
<link rel="stylesheet" href="https://fonts.googleapis.com/css2?family=Advent+Pro:wght@300;400&family=Open+Sans:wght@400;700&display=swap">
<style>
  :root {
    --rose: #b07a92;
    --rose-deep: #a66f88;
    --rose-light: #e2b8d4;
    --white: #ffffff;
    --paper: #fbfbfb;
    --backdrop: #e8e8e8;
  }
  * { box-sizing: border-box; margin: 0; padding: 0; }
  html, body { width: 1200px; height: 900px; overflow: hidden; }
  body {
    background: var(--backdrop);
    display: flex;
    flex-direction: column;
    align-items: center;
    justify-content: center;
    gap: 48px;
  }
  .card {
    position: relative;
    width: 630px;
    height: 360px;
    border-radius: 4px;
    overflow: hidden;
    box-shadow: 0 10px 28px rgba(0,0,0,0.18);
  }
  .card-front {
    background: linear-gradient(100deg, var(--rose-light) 0%, #c58fae 35%, var(--rose-deep) 70%, #a46d86 100%);
    display: flex;
    flex-direction: column;
    align-items: center;
    justify-content: center;
    color: var(--white);
  }
  .wordmark {
    font-family: "Advent Pro", sans-serif;
    font-weight: 300;
    font-size: 54px;
    letter-spacing: 0.22em;
    text-transform: uppercase;
    padding-left: 0.22em;
  }
  .card-front .wordmark { color: var(--white); }
  .front-url {
    margin-top: 26px;
    font-family: "Open Sans", sans-serif;
    font-size: 14px;
    letter-spacing: 0.32em;
  }
  .card-back { background: var(--paper); }
  .back-wave { position: absolute; inset: 0; width: 100%; height: 100%; }
  .back-brand {
    position: absolute;
    left: 60px;
    top: 190px;
  }
  .card-back .wordmark { color: var(--rose); font-size: 50px; }
  .contact {
    position: absolute;
    right: 30px;
    top: 44px;
    text-align: right;
    font-family: "Open Sans", sans-serif;
    color: var(--white);
    font-size: 13px;
    line-height: 1.42;
  }
  .contact-name { font-weight: 700; font-size: 14px; text-transform: uppercase; }
  .contact-role { margin-bottom: 12px; text-transform: uppercase; }
  .contact-line { display: flex; justify-content: flex-end; align-items: center; gap: 8px; }
  .contact-icon { width: 13px; height: 13px; flex: none; }
</style>
</head>
<body>
  <section class="card card-front" aria-label="Card front">
    <div class="wordmark">Glimora</div>
    <div class="front-url">www.glimora-example.com</div>
  </section>

  <section class="card card-back" aria-label="Card back">
    <svg class="back-wave" viewBox="0 0 630 360" preserveAspectRatio="none" aria-hidden="true">
      <path d="M470,0 C380,40 390,170 300,260 C230,325 120,335 0,345 L0,360 L630,360 L630,0 Z" fill="#b07a92"/>
      <path d="M500,0 C415,45 425,175 335,265 C265,330 150,342 20,352" fill="none" stroke="#ffffff" stroke-width="4"/>
      <path d="M455,8 C375,55 380,180 290,262 C225,320 120,330 0,338" fill="none" stroke="#b07a92" stroke-width="2" opacity="0.7"/>
    </svg>

    <div class="back-brand">
      <div class="wordmark">Glimora</div>
    </div>

    <div class="contact">
      <div class="contact-name">Mara Ellison</div>
      <div class="contact-role">CEO/Founder</div>
      <div class="contact-line">214 Linden Court</div>
      <div class="contact-line">Harbor City, Oregon 50218</div>
      <div class="contact-line">555 410 2736
        <svg class="contact-icon" viewBox="0 0 16 16" aria-hidden="true"><path d="M4 1h3l1 4-2 1c1 2 2 3 4 4l1-2 4 1v3c0 1-1 2-2 2C7 14 2 9 2 3c0-1 1-2 2-2z" fill="#fff"/></svg>
      </div>
      <div class="contact-line">555 682 1947
        <svg class="contact-icon" viewBox="0 0 16 16" aria-hidden="true"><rect x="4" y="1" width="8" height="14" rx="1.5" fill="none" stroke="#fff" stroke-width="1.6"/><circle cx="8" cy="12.5" r="0.9" fill="#fff"/></svg>
      </div>
      <div class="contact-line">555 903 5418
        <svg class="contact-icon" viewBox="0 0 16 16" aria-hidden="true"><rect x="2" y="6" width="12" height="8" rx="1" fill="#fff"/><rect x="4" y="2" width="8" height="5" fill="none" stroke="#fff" stroke-width="1.4"/></svg>
      </div>
      <div class="contact-line">info@glimora-example.com
        <svg class="contact-icon" viewBox="0 0 16 16" aria-hidden="true"><rect x="1" y="3" width="14" height="10" rx="1" fill="#fff"/><path d="M1.5 3.5 8 9l6.5-5.5" fill="none" stroke="#b07a92" stroke-width="1.3"/></svg>
      </div>
      <div class="contact-line">www.glimora-example.com
        <svg class="contact-icon" viewBox="0 0 16 16" aria-hidden="true"><circle cx="8" cy="8" r="6.5" fill="#fff"/><path d="M1.5 8h13M8 1.5c-3 3-3 10 0 13M8 1.5c3 3 3 10 0 13" fill="none" stroke="#b07a92" stroke-width="1"/></svg>
      </div>
    </div>
  </section>
</body>
</html>
```